Berufora Banner Design (Profilbanner und Unternehmensbanner) (1584 x 396) (1128 x 191)
Zielgruppe
Ich bin Dienstleister und Unternehmensberater für technischen B2B Vertrieb.
Für meinen BeruFora Account suche ich einen Banner für meine Profilseite und einen Banner für die Unternehmensseite). Meine Zielgruppe sind leitende Angestellte in Unternehmen. Das Design sollte entsprechend grafisch hochwertig, seriös gestaltet sein.
I am a service provider and management consultant for technical B2B sales.
For my BeruFora account, I'm looking for a banner for my profile page and a banner for the company page). My target group are executives in companies. The design should have a correspondingly high-quality graphic design and be serious.
Aufgabenstellung
Wichtig ist die Berücksichtigung meines Logos (PNG im Anhang) und des Corporate Identity Farben (PDF Anhang und unten stehend). Stock Bilder oder Grafiken können/sollen gerne mit eingebunden werden. Wichtig ist hier der passende Gesamteindruck.
It is important to consider my logo (PNG in the attachment) and the corporate identity colors (PDF attachment and below). Stock images or graphics can/should be included. The right overall impression is important here.
HEX / HTML 002854
HEX / HTML 00b6e3
Bannergrößen / Banner sizes
Profilbanner (1584 x 396)
Unternehmensseitenbanner (1128 x 191)

```html
<!DOCTYPE html>
<html lang="de">
<head>
<meta charset="utf-8">
<title>Lennart Vossberg Management &amp; Sales Consulting GmbH – Unternehmensseite</title>
<link rel="stylesheet" href="https://fonts.googleapis.com/css2?family=Titillium+Web:wght@300;400;600;700&family=Source+Sans+3:wght@400;600&display=swap">
<style>
  :root {
    --brand-navy: #002854;
    --brand-cyan: #00b6e3;
    --banner-deep: #0615b8;
    --banner-bright: #1a3dff;
    --engine-dark: #15181f;
    --engine-light: #6a7080;
    --white: #ffffff;
    --text-main: #1d1d1d;
    --text-sub: #3c3c3c;
    --text-meta: #6b6b6b;
    --action-blue: #0a66c2;
    --outline-grey: #6b6b6b;
  }
  * { box-sizing: border-box; margin: 0; padding: 0; }
  html, body { width: 1200px; height: 656px; overflow: hidden; background: var(--white); }
  .page { position: relative; width: 1200px; height: 656px; font-family: "Source Sans 3", Arial, sans-serif; }

  .cover {
    position: absolute; left: 0; top: 0; width: 1200px; height: 303px;
    background: linear-gradient(100deg, var(--banner-deep) 0%, #0a22e0 45%, var(--banner-bright) 75%, #1030f0 100%);
    overflow: hidden;
  }
  .cover__line { position: absolute; height: 2px; background: rgba(90,150,255,0.45); }
  .cover__headline {
    position: absolute; left: 300px; top: 44px;
    font-family: "Titillium Web", Arial, sans-serif; color: var(--white);
    text-transform: uppercase; line-height: 1;
  }
  .cover__headline span { display: block; }
  .cover__headline .line-one { font-size: 36px; font-weight: 300; }
  .cover__headline .line-two { font-size: 36px; font-weight: 300; margin: 18px 0 0 39px; }
  .cover__headline b { font-weight: 700; font-size: 42px; }
  .cover__contact {
    position: absolute; left: 232px; top: 263px; display: flex; align-items: center; gap: 22px;
    font-family: "Titillium Web", Arial, sans-serif; font-weight: 600; font-size: 15px; color: var(--white);
  }
  .contact-item { display: flex; align-items: center; gap: 9px; }
  .cover__engine {
    position: absolute; left: 700px; top: -20px; width: 520px; height: 343px;
    background: radial-gradient(ellipse 60% 62% at 45% 55%, #dfe3ea 0%, var(--engine-light) 20%, var(--engine-dark) 50%, rgba(21,24,31,0.85) 75%, rgba(21,24,31,0) 100%);
  }

  .company-logo {
    position: absolute; left: 38px; top: 213px; width: 168px; height: 165px;
    background: var(--brand-navy); border: 2px solid var(--white);
    display: flex; align-items: center; justify-content: center; text-align: center;
    font-family: "Source Sans 3", Arial, sans-serif; font-weight: 600; font-size: 20px; line-height: 1.15;
    color: var(--brand-cyan);
  }

  .company-name { position: absolute; left: 35px; top: 397px; font-size: 39px; line-height: 1.2; font-weight: 600; color: var(--text-main); white-space: nowrap; }
  .company-tagline { position: absolute; left: 35px; top: 445px; font-size: 26px; line-height: 1.2; color: var(--text-sub); white-space: nowrap; }
  .company-meta { position: absolute; left: 34px; top: 480px; font-size: 22px; line-height: 1.2; color: var(--text-meta); white-space: nowrap; }
  .company-staff { position: absolute; left: 35px; top: 525px; font-size: 25px; line-height: 1.2; font-weight: 600; color: var(--text-meta); white-space: nowrap; }

  .actions { position: absolute; left: 35px; top: 583px; display: flex; gap: 13px; }
  .btn {
    height: 49px; border-radius: 25px; display: flex; align-items: center; justify-content: center; gap: 10px;
    font-size: 24px; font-weight: 600;
  }
  .btn--follow { width: 210px; background: var(--action-blue); color: var(--white); }
  .btn--website { width: 292px; border: 1.5px solid var(--action-blue); color: var(--action-blue); }
  .btn--more { width: 110px; border: 1.5px solid var(--outline-grey); color: var(--outline-grey); }
</style>
</head>
<body>
<div class="page">
  <header class="cover">
    <div class="cover__line" style="left:0;top:135px;width:250px;"></div>
    <div class="cover__line" style="left:60px;top:210px;width:520px;"></div>
    <div class="cover__line" style="left:300px;top:240px;width:260px;"></div>
    <div class="cover__engine" role="img" aria-label="Foto eines Automotors vor blauem Hintergrund"></div>
    <h1 class="cover__headline">
      <span class="line-one">Volle <b>Power</b></span>
      <span class="line-two">Für ihr <b>Business</b>.</span>
    </h1>
    <div class="cover__contact">
      <span class="contact-item">
        <svg width="24" height="24" viewBox="0 0 24 24" fill="none" stroke="#fff" stroke-width="1.6" stroke-linejoin="round"><path d="M5 3l4 1 1.5 4.5-2.5 1.5a12 12 0 0 0 6 6l1.5-2.5L20 15l1 4-2 2C10 21 3 14 3 5z"/></svg>
        0987 | 654 321 0
      </span>
      <span class="contact-item">
        <svg width="24" height="24" viewBox="0 0 24 24" fill="none" stroke="#fff" stroke-width="1.5"><circle cx="12" cy="12" r="10"/><ellipse cx="12" cy="12" rx="4.5" ry="10"/><path d="M2 12h20M4 7h16M4 17h16"/></svg>
        VOSSBERG-CONSULT.DE
      </span>
    </div>
  </header>

  <div class="company-logo">Lennart<br>Vossberg</div>

  <h2 class="company-name">Lennart Vossberg Management &amp; Sales Consulting GmbH</h2>
  <p class="company-tagline">B2B Sales Consulting</p>
  <p class="company-meta">Business Consulting und Unternehmensdienstleistungen · Wiesenfeld, North Rhine-Westphalia · 1 Follower</p>
  <p class="company-staff">1 Mitarbeiter:in auf BeruFora ansehen</p>

  <div class="actions">
    <span class="btn btn--follow">+ Folgen</span>
    <span class="btn btn--website">Website besuchen
      <svg width="22" height="22" viewBox="0 0 24 24" fill="none" stroke="#0a66c2" stroke-width="2.6" stroke-linecap="round"><path d="M10 5H5v14h14v-5"/><path d="M13 3h8v8M21 3L11 13"/></svg>
    </span>
    <span class="btn btn--more">Mehr</span>
  </div>
</div>
</body>
</html>
```